Design a web site for my business - Brightline Coatings Co.

We are a family business that handles design, fabrication and installation of powder coated aluminum, stainless steel and glass products. Including handrails, privacy slat screens, electric gates and pool fencing. We are based in the Whitsundays in North Queensland and service an area from Airlie Beach to Townsville.

Target Market(s)

Domestic and commercial

Industry/Entity Type

fabrication - manufacturing

Coding

Coded - Design and coding required

Number of Pages Required

5+ page

Colors
0054AA
0677BA
7BADD7
CADEEF
E8F1F8

Requirements
Must have
• photo galleries, contact page, one page for privacy screens, balustrades, glass fencing, stainless steel handrail, powder coated aluminium handrails and pool fencing

```html
<!DOCTYPE html>
<html lang="en">
<head>
<meta charset="utf-8">
<title>Brightline Coatings Co – Fencing, Handrails &amp; Gates</title>
<link href="https://fonts.googleapis.com/css2?family=Inter:wght@400;500;600;700;800&display=swap" rel="stylesheet">
<style>
:root{
  --navy:#2f4a6b;
  --navy-dark:#34506e;
  --ink:#1b1f24;
  --muted:#4a5159;
  --pale:#e8f1f8;
  --line:#cfd6de;
  --sage:#4f6a62;
  --white:#ffffff;
  --icon-tint:#dbe3ec;
}
*{box-sizing:border-box;margin:0;padding:0}
html,body{width:1200px;height:5277px;overflow:hidden}
body{font-family:"Inter",sans-serif;color:var(--ink);background:var(--white)}
.wrap{width:984px;margin:0 auto;position:relative}
.btn{display:inline-flex;align-items:center;gap:8px;border-radius:8px;font-weight:600;font-size:15px;text-decoration:none;color:var(--white);background:var(--navy);padding:0 16px;height:44px;white-space:nowrap}
.btn svg{width:15px;height:15px}

/* nav */
.nav{height:80px;border-bottom:1px solid var(--line)}
.nav .wrap{display:flex;align-items:center;justify-content:space-between;height:80px}
.brand{display:flex;align-items:center;gap:12px;font-weight:700;font-size:17px;color:var(--navy)}
.brand i{width:44px;height:44px;border-radius:50%;background:var(--navy);display:block}
.menu{display:flex;align-items:center;gap:24px;font-size:15px}
.menu a{color:var(--ink);text-decoration:none}
.menu .btn{color:var(--white)}

/* hero */
.hero{height:634px;background:linear-gradient(100deg,#2a3e5c 0%,#4d6686 45%,#9aa9b8 75%,#c9d1d8 100%)}
.hero .wrap{padding-top:135px;color:var(--white)}
.hero h1{font-size:66px;line-height:75px;font-weight:800;width:560px;letter-spacing:-.5px}
.hero p{font-size:18px;font-weight:600;margin-top:40px}
.hero .actions{display:flex;gap:14px;margin-top:30px}
.hero .ghost{background:rgba(255,255,255,.12);border:1px solid rgba(255,255,255,.5)}

/* about */
.about{height:690px}
.about .wrap{display:flex;justify-content:space-between;align-items:center;height:690px}
.about h2{font-size:38px;line-height:46px;font-weight:700;width:470px}
.about p{font-size:15px;line-height:22px;color:var(--muted);width:400px;margin-top:24px}
.ticks{list-style:none;margin-top:18px}
.ticks li{display:flex;align-items:center;gap:14px;font-size:18px;margin-bottom:22px}
.ticks svg{width:16px;height:16px}
.about-photo{position:relative;width:520px;height:520px;display:flex;align-items:center;justify-content:flex-end}
.about-photo .frame{position:absolute;left:10px;top:30px;width:480px;height:470px;border:1.5px solid #9aa4b0;border-radius:30px;transform:rotate(8deg)}
.about-photo .img{position:relative;width:478px;height:454px;border-radius:26px;background:linear-gradient(150deg,#3d4752,#8a96a2 50%,#5c6772);box-shadow:0 10px 24px rgba(0,0,0,.2)}

/* services */
.services{height:850px;background:var(--pale);text-align:center}
.services h2{font-size:40px;font-weight:700;padding-top:120px}
.lead{font-size:16px;color:var(--muted);margin-top:22px;line-height:23px}
.cards{display:grid;grid-template-columns:repeat(3,316px);gap:18px;margin-top:66px}
.card{height:197px;background:var(--white);border:1px solid #aeb6bf;border-radius:18px;display:flex;flex-direction:column;align-items:center;justify-content:flex-end;padding-bottom:28px}
.card .icon{width:96px;height:84px;margin-bottom:24px;border-radius:12px;background:linear-gradient(160deg,var(--icon-tint),#c3cfdc)}
.card span{font-size:19px;font-weight:500}
.services .btn{margin-top:56px;height:42px}

/* materials */
.materials{height:780px;text-align:center}
.materials h2{font-size:36px;font-weight:700;padding-top:120px}
.grid3{display:grid;grid-template-columns:repeat(3,316px);gap:18px;margin-top:40px}
.mat .img{height:256px;border-radius:14px}
.mat h3{font-size:19px;font-weight:500;margin-top:30px}
.mat p{font-size:14px;line-height:23px;color:var(--muted);margin-top:8px;padding:0 10px}

/* gallery */
.gallery{height:896px;background:var(--pale);text-align:center}
.gallery h2{font-size:38px;font-weight:700;padding-top:110px}
.gal{display:grid;grid-template-columns:repeat(3,316px);grid-template-rows:254px 254px;gap:13px 18px;margin-top:40px}
.gal div{border-radius:12px}
.gal .tall{grid-row:span 2}

/* contact */
.contact{height:812px}
.contact .wrap{display:flex;justify-content:space-between;padding-top:140px}
.contact h2{font-size:38px;line-height:46px;font-weight:700}
.contact .lead{text-align:left;width:390px;font-size:15px;line-height:22px;margin-top:26px}
.info{margin-top:22px;width:440px}
.info .row{display:flex;align-items:center;gap:18px;border:1px solid #dde2e7;border-radius:14px;height:76px;padding:0 18px;margin-bottom:12px}
.info .ico{width:42px;height:42px;border-radius:50%;background:#8b949e;display:flex;align-items:center;justify-content:center;flex:none}
.info .ico svg{width:20px;height:20px}
.info small{display:block;font-size:14px;color:#7a828b}
.info b{font-size:16px;font-weight:500;white-space:nowrap}
.map{width:517px;height:533px;border-radius:26px;background:linear-gradient(160deg,#a9d4ee 0%,#9fcfe6 40%,#cfe6cf 70%,#e6efe2 100%);border:1px solid #c7ccd2}

/* cta */
.cta{height:223px;background:var(--sage);color:var(--white)}
.cta .wrap{display:flex;justify-content:space-between;align-items:center;height:223px}
.cta h2{font-size:38px;line-height:46px;font-weight:700}
.cta p{font-size:15px;line-height:22px;margin-top:12px;width:450px;color:#e6ecea}
.cta .actions{display:flex;gap:18px}
.cta .btn{background:var(--navy)}
.cta .ghost{background:transparent;border:1px solid rgba(255,255,255,.55)}

/* footer */
.footer{height:312px;background:var(--navy-dark);color:var(--white)}
.footer .cols{display:flex;padding-top:60px;height:262px}
.footer .col1{width:416px}
.footer .col1 .brand{color:var(--white);font-size:22px}
.footer .col1 .brand i{background:#ffffff}
.footer .col1 p{font-size:12px;line-height:18px;color:#d4dce5;margin-top:24px;width:330px}
.footer h4{font-size:15px;font-weight:600;margin-bottom:12px}
.footer .col2{width:252px;font-size:13px;color:#d4dce5}
.footer .col2 div{display:flex;gap:14px;margin-bottom:18px;line-height:18px}
.footer .col2 svg{width:16px;height:16px;flex:none}
.footer table{font-size:13px;color:#d4dce5;border-spacing:0}
.footer td{padding:0 0 14px;width:148px}
.copy{text-align:center;font-size:13px;color:#d4dce5}
</style>
</head>
<body>

<header class="nav">
  <div class="wrap">
    <div class="brand"><i></i>Brightline Coatings Co</div>
    <nav class="menu">
      <a href="#">About</a><a href="#">Services</a><a href="#">Materials</a><a href="#">Gallery</a><a href="#">Contact</a>
      <a class="btn" href="#"><svg viewBox="0 0 24 24" fill="#fff"><path d="M6.6 10.8a15 15 0 006.6 6.6l2.2-2.2a1 1 0 011-.25 11.4 11.4 0 003.6.57 1 1 0 011 1V20a1 1 0 01-1 1A17 17 0 013 4a1 1 0 011-1h3.5a1 1 0 011 1c0 1.25.2 2.45.57 3.57a1 1 0 01-.25 1z"/></svg>Call Now</a>
    </nav>
  </div>
</header>

<section class="hero" role="img" aria-label="Close-up of polished stainless steel handrail posts">
  <div class="wrap">
    <h1>Quality Fencing, Handrails &amp; Gates</h1>
    <p>Fabricated In The Whitsundays</p>
    <div class="actions">
      <a class="btn" href="#">Get a Free Quote</a>
      <a class="btn ghost" href="#"><svg viewBox="0 0 24 24" fill="#fff"><path d="M6.6 10.8a15 15 0 006.6 6.6l2.2-2.2a1 1 0 011-.25 11.4 11.4 0 003.6.57 1 1 0 011 1V20a1 1 0 01-1 1A17 17 0 013 4a1 1 0 011-1h3.5a1 1 0 011 1c0 1.25.2 2.45.57 3.57a1 1 0 01-.25 1z"/></svg>07 4000 1234</a>
    </div>
  </div>
</section>

<section class="about">
  <div class="wrap">
    <div>
      <h2>A Reliable Fencing Partner, Made Right Here In Cannonvale</h2>
      <p>Brightline Coatings Co is a local, family-owned fence contractor based in Cannonvale. We design, fabricate and install high-quality...</p>
      <ul class="ticks">
        <li><svg viewBox="0 0 16 16" fill="none" stroke="#2f4a6b" stroke-width="1.5"><rect x="1" y="1" width="14" height="14" rx="2"/><path d="M4 8l3 3 5-6"/></svg>Design, fabrication &amp; installation</li>
        <li><svg viewBox="0 0 16 16" fill="none" stroke="#2f4a6b" stroke-width="1.5"><rect x="1" y="1" width="14" height="14" rx="2"/><path d="M4 8l3 3 5-6"/></svg>Premium, durable materials</li>
        <li><svg viewBox="0 0 16 16" fill="none" stroke="#2f4a6b" stroke-width="1.5"><rect x="1" y="1" width="14" height="14" rx="2"/><path d="M4 8l3 3 5-6"/></svg>Jobs big and small</li>
        <li><svg viewBox="0 0 16 16" fill="none" stroke="#2f4a6b" stroke-width="1.5"><rect x="1" y="1" width="14" height="14" rx="2"/><path d="M4 8l3 3 5-6"/></svg>Consultation &amp; advice</li>
      </ul>
    </div>
    <div class="about-photo">
      <div class="frame"></div>
      <div class="img" role="img" aria-label="Curved stainless steel balustrade on a walkway"></div>
    </div>
  </div>
</section>

<section class="services">
  <div class="wrap">
    <h2>Design, Fabrication &amp; Installation</h2>
    <p class="lead">Whatever your project, our in-house team designs and manufactures it at our Cannonvale factory.</p>
    <div class="cards">
      <div class="card"><div class="icon" role="img" aria-label="Line illustration of a pool fence"></div><span>Pool Fencing</span></div>
      <div class="card"><div class="icon" role="img" aria-label="Line illustration of a stair balustrade"></div><span>Handrails &amp; Balustrades</span></div>
      <div class="card"><div class="icon" role="img" aria-label="Line illustration of an automated gate"></div><span>Electric &amp; Automated Gates</span></div>
      <div class="card"><div class="icon" role="img" aria-label="Line illustration of a house with a privacy screen"></div><span>Privacy Slat Screens</span></div>
      <div class="card"><div class="icon" role="img" aria-label="Line illustration of a fence panel"></div><span>Fencing</span></div>
      <div class="card"><div class="icon" role="img" aria-label="Line illustration of a fabrication plan and tool"></div><span>Custom Fabrication</span></div>
    </div>
    <a class="btn" href="#">Enquiry Now <svg viewBox="0 0 16 16" fill="none" stroke="#fff" stroke-width="1.8"><path d="M2 8h11M9 4l4 4-4 4"/></svg></a>
  </div>
</section>

<section class="materials">
  <div class="wrap">
    <h2>Built To Last In The Tropics</h2>
    <p class="lead">We specialise in three premium materials, each finished and fabricated to handle the<br>coastal Whitsundays climate.</p>
    <div class="grid3">
      <div class="mat"><div class="img" role="img" aria-label="White powder coated aluminium stair balustrade" style="background:linear-gradient(140deg,#e7e2da,#8d6b52 60%,#5b4333)"></div><h3>Powder Coated Aluminium</h3><p>Corrosion-resistant and endlessly versatile, finished in a huge range of colours to suit the coastal environment.</p></div>
      <div class="mat"><div class="img" role="img" aria-label="Stainless steel handrail posts against a blue sky" style="background:linear-gradient(180deg,#8fb4d8,#c9d8e6 55%,#8e9aa5)"></div><h3>Stainless Steel</h3><p>Marine-grade stainless steel for strength and a premium, contemporary finish that stands up to the tropics.</p></div>
      <div class="mat"><div class="img" role="img" aria-label="Frameless glass balustrade on a terrace" style="background:linear-gradient(170deg,#4d86c6,#a9c9e6 50%,#6f7e72)"></div><h3>Glass</h3><p>Frameless and semi-frameless glass for an elegant, uninterrupted view without compromising on safety.</p></div>
    </div>
  </div>
</section>

<section class="gallery">
  <div class="wrap">
    <h2>Craftsmanship You Can See</h2>
    <p class="lead">A glimpse at the finishes and details we’re proud to put our name on — quality<br>materials, clean lines and a flawless powder coated finish.</p>
    <div class="gal">
      <div class="tall" role="img" aria-label="Black aluminium fence beneath a white shade structure" style="background:linear-gradient(180deg,#6fa0d6,#dfe3e6 45%,#2c3136 75%,#a88a70)"></div>
      <div role="img" aria-label="Timber slat entry door with dark screening" style="background:linear-gradient(135deg,#3a3029,#9c8a78 60%,#d6d4cf)"></div>
      <div role="img" aria-label="Glass pool fence with palms behind" style="background:linear-gradient(170deg,#6d9fcf,#8eaa88 55%,#c9d5d5)"></div>
      <div role="img" aria-label="Timber stairs with black steel balustrade" style="background:linear-gradient(140deg,#2b2c2e,#8a4a28 55%,#e3e2df)"></div>
      <div role="img" aria-label="Black fence along a driveway under a shade sail" style="background:linear-gradient(180deg,#7aa6d8,#e3e4e2 45%,#2e3338 72%,#b89a7e)"></div>
    </div>
  </div>
</section>

<section class="contact">
  <div class="wrap">
    <div>
      <h2>Let's Talk About<br>Your Project</h2>
      <p class="lead">Call, email or drop by the factory — we’re happy to provide advice and a free quote for jobs big and small.</p>
      <div class="info">
        <div class="row"><div class="ico"><svg viewBox="0 0 24 24" fill="#fff"><path d="M6.6 10.8a15 15 0 006.6 6.6l2.2-2.2a1 1 0 011-.25 11.4 11.4 0 003.6.57 1 1 0 011 1V20a1 1 0 01-1 1A17 17 0 013 4a1 1 0 011-1h3.5a1 1 0 011 1c0 1.25.2 2.45.57 3.57a1 1 0 01-.25 1z"/></svg></div><div><small>Phone</small><b>07 4000 1234</b></div></div>
        <div class="row"><div class="ico"><svg viewBox="0 0 24 24" fill="#fff"><path d="M3 5h18v14H3z"/><path d="M3 5l9 7 9-7" stroke="#8b949e" stroke-width="2" fill="none"/></svg></div><div><small>Email</small><b>office@brightlinecoat.com.au</b></div></div>
        <div class="row"><div class="ico"><svg viewBox="0 0 24 24" fill="#fff"><path d="M12 2a7 7 0 00-7 7c0 5 7 13 7 13s7-8 7-13a7 7 0 00-7-7zm0 9.5A2.5 2.5 0 1112 6.5a2.5 2.5 0 010 5z"/></svg></div><div><small>Visit the factory</small><b>12 Harbour Crest Rd, Cannonvale QLD 4802</b></div></div>
        <div class="row"><div class="ico"><svg viewBox="0 0 24 24" fill="none" stroke="#fff" stroke-width="2"><circle cx="12" cy="12" r="9"/><path d="M12 7v5l3 2"/></svg></div><div><small>Opening hours</small><b>Mon–Fri 7:30am – 4:00pm</b></div></div>
      </div>
    </div>
    <div class="map" role="img" aria-label="Map showing the factory location in Cannonvale"></div>
  </div>
</section>

<section class="cta">
  <div class="wrap">
    <div>
      <h2>Ready To Start Your<br>Fencing Project?</h2>
      <p>Get in touch for a free, no-obligation quote. Locally made in Cannonvale, installed across the Whitsundays.</p>
    </div>
    <div class="actions">
      <a class="btn" href="#">Email Us</a>
      <a class="btn ghost" href="#"><svg viewBox="0 0 24 24" fill="#fff"><path d="M6.6 10.8a15 15 0 006.6 6.6l2.2-2.2a1 1 0 011-.25 11.4 11.4 0 003.6.57 1 1 0 011 1V20a1 1 0 01-1 1A17 17 0 013 4a1 1 0 011-1h3.5a1 1 0 011 1c0 1.25.2 2.45.57 3.57a1 1 0 01-.25 1z"/></svg>07 4000 1234</a>
    </div>
  </div>
</section>

<footer class="footer">
  <div class="wrap">
    <div class="cols">
      <div class="col1">
        <div class="brand"><i></i>Brightline Coatings Co</div>
        <p>Family-owned fencing contractors specialising in powder coated aluminium, stainless steel and glass for the Whitsundays and beyond.</p>
      </div>
      <div class="col2">
        <h4>Contact</h4>
        <div><svg viewBox="0 0 24 24" fill="#fff"><path d="M12 2a7 7 0 00-7 7c0 5 7 13 7 13s7-8 7-13a7 7 0 00-7-7zm0 9.5A2.5 2.5 0 1112 6.5a2.5 2.5 0 010 5z"/></svg>12 Harbour Crest Rd,<br>Cannonvale QLD 4802</div>
        <div><svg viewBox="0 0 24 24" fill="#fff"><path d="M6.6 10.8a15 15 0 006.6 6.6l2.2-2.2a1 1 0 011-.25 11.4 11.4 0 003.6.57 1 1 0 011 1V20a1 1 0 01-1 1A17 17 0 013 4a1 1 0 011-1h3.5a1 1 0 011 1c0 1.25.2 2.45.57 3.57a1 1 0 01-.25 1z"/></svg>07 4000 1234</div>
        <div><svg viewBox="0 0 24 24" fill="#fff"><path d="M3 5h18v14H3z"/><path d="M3 5l9 7 9-7" stroke="#34506e" stroke-width="2" fill="none"/></svg>office@brightlinecoat.com.au</div>
      </div>
      <div>
        <h4>Hours</h4>
        <table>
          <tr><td>Mon – Fri</td><td>7:30am – 4:00pm</td></tr>
          <tr><td>Saturday</td><td>By appointment</td></tr>
          <tr><td>Sunday</td><td>Closed</td></tr>
        </table>
      </div>
    </div>
    <p class="copy">© 2026 Brightline Coatings Co. All rights reserved.</p>
  </div>
</footer>

</body>
</html>
```